Agriculture Business Card

I want to use my existing logo and use my tagline of "Don't Guess...Soil Test" on the card. Looking for a double sided card that will really get peoples attention.
Contact Info:
Marlow Field Crop Edge
Calvin Brusk
2917 K Lane
Larkin, NE 68593
402-555-0193
calvin.r.brusk@fieldmailbox.net

```html
<!DOCTYPE html>
<html lang="en">
<head>
<meta charset="utf-8">
<title>Marlow Field Crop Edge – Business Card</title>
<link href="https://fonts.googleapis.com/css2?family=Oswald:wght@500;600&family=Roboto:wght@400&display=swap" rel="stylesheet">
<style>
  :root{
    --bg:#a9b0b3;
    --card:#ede7e3;
    --brown:#8c4a26;
    --edge:#6b3a1f;
    --ink:#4a4644;
    --green:#3fae29;
    --gold:#f0a81c;
  }
  html,body{margin:0;padding:0;overflow:hidden;}
  body{width:1200px;height:837px;background:var(--bg);position:relative;font-family:'Roboto',sans-serif;}
  .card{position:absolute;background:var(--card);box-shadow:0 3px 0 var(--edge),0 10px 24px rgba(0,0,0,.18);}
  .card--back{left:170px;top:150px;width:300px;height:525px;display:flex;flex-direction:column;align-items:center;text-align:center;}
  .card--front{left:560px;top:268px;width:525px;height:300px;display:flex;align-items:center;justify-content:center;}
  .person-name{font-family:'Oswald',sans-serif;font-weight:600;color:var(--brown);font-size:27px;letter-spacing:1px;margin:92px 0 10px;}
  .icon{width:20px;height:20px;border-radius:50%;background:var(--brown);display:inline-flex;align-items:center;justify-content:center;}
  .icon svg{width:12px;height:12px;}
  .icon-row{display:flex;gap:5px;margin:12px 0 10px;}
  .address,.contact{color:var(--ink);font-size:16px;line-height:20px;margin-top:8px;}
  .contact{margin-top:0;font-size:15px;}
  .tagline{margin-top:22px;width:235px;border-top:1.5px solid var(--gold);border-bottom:1.5px solid var(--brown);padding:7px 0 5px;font-family:'Oswald',sans-serif;font-weight:600;font-size:21px;letter-spacing:.5px;}
  .tagline .guess{color:var(--green);}
  .tagline .test{color:var(--gold);}
  .brand{display:flex;align-items:center;gap:8px;font-family:'Oswald',sans-serif;font-weight:600;color:var(--brown);}
  .brand-dot{width:14px;height:14px;border-radius:50%;background:var(--gold);flex:none;}
  .card--back .brand{margin-top:34px;font-size:17px;}
  .card--front .brand{font-size:30px;}
</style>
</head>
<body>
  <section class="card card--back">
    <div class="person-name">CALVIN BRUSK</div>
    <span class="icon"><svg viewBox="0 0 12 12"><path d="M6 1a3.5 3.5 0 0 0-3.5 3.5C2.5 7.2 6 11 6 11s3.5-3.8 3.5-6.5A3.5 3.5 0 0 0 6 1zm0 4.8a1.3 1.3 0 1 1 0-2.6 1.3 1.3 0 0 1 0 2.6z" fill="#ede7e3"/></svg></span>
    <div class="address">2917 K Lane<br>Larkin, NE 68593</div>
    <div class="icon-row">
      <span class="icon"><svg viewBox="0 0 12 12"><path d="M3 1.5l1.8 2-1 1.2a7 7 0 0 0 3.5 3.5l1.2-1 2 1.8-1.2 1.5C5.5 10.3 1.7 6.5 1.5 2.7z" fill="#ede7e3"/></svg></span>
      <span class="icon"><svg viewBox="0 0 12 12"><rect x="1.5" y="3" width="9" height="6" fill="none" stroke="#ede7e3" stroke-width="1.2"/><path d="M1.5 3L6 6.5 10.5 3" fill="none" stroke="#ede7e3" stroke-width="1.2"/></svg></span>
      <span class="icon"><svg viewBox="0 0 12 12"><circle cx="6" cy="6" r="4.3" fill="none" stroke="#ede7e3" stroke-width="1.1"/><path d="M1.7 6h8.6M6 1.7c-2 2.4-2 6.2 0 8.6M6 1.7c2 2.4 2 6.2 0 8.6" fill="none" stroke="#ede7e3" stroke-width="1"/></svg></span>
    </div>
    <div class="contact">402-555-0193<br>calvin.r.brusk@fieldmailbox.net<br>marlowfieldcrop.com</div>
    <div class="tagline"><span class="guess">DON'T GUESS...</span><span class="test">SOIL TEST</span></div>
    <div class="brand"><span class="brand-dot"></span>Marlow Field Crop Edge</div>
  </section>

  <section class="card card--front">
    <div class="brand"><span class="brand-dot"></span>Marlow Field Crop Edge</div>
  </section>
</body>
</html>
```